Building technology company seek stationery design and folder design

Letterhead, and a folder design
ideally, I would have two letter head design, one is for one-page bussiness letter. the other one I can use for longer document such report, or analysis regular report page
you can find company logo and overall style at our website:
www.structavolt.example

we are in building technology business, using internet of things technology to improve building energy efficiency to make building greener.

Industry/Entity Type

It Company

Requirements
Must have
• company logo
Nice to have
• techy look abstract graphics, etc.
Should not have
• no comment

```html
<!DOCTYPE html>
<html lang="en">
<head>
<meta charset="utf-8">
<title>Structavolt Stationery</title>
<link rel="stylesheet" href="https://fonts.googleapis.com/css2?family=Questrial&display=swap">
<style>
  :root {
    --canvas: #dcdcdc;
    --paper-light: #ffffff;
    --paper-shade: #eeeeee;
    --band-olive: #7a7a68;
    --brand-green: #a6cf3a;
    --folder-green: #b1d44e;
    --folder-line: #c3df72;
    --ink: #444444;
    --ink-soft: #666666;
  }
  * { margin: 0; padding: 0; box-sizing: border-box; }
  html, body { width: 1200px; height: 821px; overflow: hidden; background: var(--canvas); }
  body { position: relative; font-family: "Questrial", sans-serif; color: var(--ink); }

  .letterhead {
    position: absolute; left: 75px; top: 114px; width: 441px; height: 620px;
    background: linear-gradient(90deg, var(--paper-light) 0%, var(--paper-shade) 100%);
    overflow: hidden;
    box-shadow: 0 1px 3px rgba(0,0,0,0.12);
  }
  .letterhead__band { position: absolute; left: 0; width: 441px; z-index: 2; }
  .letterhead__band--top { top: 0; height: 20px; }
  .letterhead__band--bottom { bottom: 0; height: 20px; }

  .letterhead__brand {
    position: absolute; left: 37px; top: 82px;
    font-size: 13px; letter-spacing: 1px; color: var(--brand-green);
  }
  .contact-list {
    position: absolute; left: 313px; top: 46px; list-style: none;
    font-size: 6.2px; line-height: 9px; color: var(--ink-soft);
  }
  .contact-list li { display: flex; align-items: center; gap: 4px; }
  .contact-list svg { width: 6px; height: 6px; fill: var(--brand-green); }

  .letter { position: absolute; left: 39px; top: 176px; width: 366px; z-index: 1; }
  .letter__salutation { font-size: 11px; color: var(--ink); margin-bottom: 18px; }
  .letter__body p {
    font-size: 5.8px; line-height: 9.6px; color: var(--ink-soft);
    margin-bottom: 9.6px; text-align: justify;
  }
  .letter__closing { font-size: 6px; color: var(--ink-soft); margin-top: 18px; }
  .letter__signature {
    width: 80px; height: 30px; margin-top: 10px;
    background: radial-gradient(ellipse at 45% 55%, rgba(166,207,58,0.28) 0%, rgba(166,207,58,0) 70%);
  }
  .letterhead__circuit {
    position: absolute; left: 0; top: 360px; width: 441px; height: 260px;
    background: linear-gradient(150deg, rgba(190,190,190,0) 25%, rgba(190,190,190,0.16) 60%, rgba(190,190,190,0.08) 100%);
    -webkit-mask-image: radial-gradient(ellipse 75% 80% at 60% 70%, #000 35%, transparent 100%);
    mask-image: radial-gradient(ellipse 75% 80% at 60% 70%, #000 35%, transparent 100%);
  }

  .folder {
    position: absolute; left: 553px; top: 77px; width: 520px; height: 659px;
    background: var(--folder-green); overflow: hidden;
    box-shadow: 0 1px 3px rgba(0,0,0,0.12);
  }
  .folder__spine { position: absolute; top: 0; left: 0; width: 40px; height: 659px; }
  .folder__brand {
    position: absolute; left: 0; top: 148px; width: 520px; text-align: center;
    font-size: 32px; letter-spacing: 3px; color: #ffffff;
  }
  .folder__circuit {
    position: absolute; left: 0; top: 290px; width: 520px; height: 369px;
    background: linear-gradient(150deg, rgba(200,226,120,0) 20%, rgba(200,226,120,0.45) 60%, rgba(200,226,120,0.25) 100%);
    -webkit-mask-image: radial-gradient(ellipse 80% 80% at 55% 70%, #000 30%, transparent 100%);
    mask-image: radial-gradient(ellipse 80% 80% at 55% 70%, #000 30%, transparent 100%);
  }
</style>
</head>
<body>

<section class="letterhead">
  <svg class="letterhead__band letterhead__band--top" viewBox="0 0 441 20" preserveAspectRatio="none">
    <polygon points="0,0 441,0 441,4 0,20" fill="var(--band-olive)"/>
  </svg>

  <div class="letterhead__brand">STRUCTAVOLT</div>

  <ul class="contact-list">
    <li><svg viewBox="0 0 10 10"><path d="M2 1l2 0 1 2.5-1.2 1a6 6 0 0 0 2.7 2.7l1-1.2L10 7v2a1 1 0 0 1-1 1A9 9 0 0 1 0 1a1 1 0 0 1 1-1z"/></svg>(555) 014-2290</li>
    <li><svg viewBox="0 0 10 10"><rect x="0" y="2" width="10" height="7"/></svg>info@structavolt.example</li>
    <li><svg viewBox="0 0 10 10"><circle cx="5" cy="5" r="4.5"/></svg>www.structavolt.example</li>
    <li><svg viewBox="0 0 10 10"><rect x="1" y="1" width="8" height="8"/></svg>structavolt</li>
  </ul>

  <div class="letterhead__circuit" role="img" aria-label="Faint grey circuit-line pattern"></div>

  <article class="letter">
    <p class="letter__salutation">Dear Mr. Carter,</p>
    <div class="letter__body">
      <p>Thank you for meeting with our team last week. This letter confirms the scope of the sensor pilot planned for your office tower. We will install connected meters on each floor, track heating and cooling loads in real time, and share a weekly summary with your facilities staff. The first review is set for the end of next month.</p>
      <p>During the pilot our engineers will tune schedules for lighting, ventilation and pumps. Any change will be agreed with your building manager before it goes live. Data stays on secure servers and you may export it at any time in common formats.</p>
      <p>Based on similar sites, we expect energy use to fall by twelve to eighteen percent within the first year. Savings will be measured against last year's utility bills, adjusted for weather and occupancy, so results are fair and easy to verify.</p>
      <p>Please review the enclosed plan and let us know of any questions. We look forward to working with you.</p>
    </div>
    <p class="letter__closing">Sincerely,</p>
    <div class="letter__signature" role="img" aria-label="Handwritten signature of Dana Carter"></div>
  </article>

  <svg class="letterhead__band letterhead__band--bottom" viewBox="0 0 441 20" preserveAspectRatio="none">
    <polygon points="0,18 441,0 441,20 0,20" fill="var(--brand-green)"/>
  </svg>
</section>

<section class="folder">
  <svg class="folder__spine" viewBox="0 0 40 659" preserveAspectRatio="none">
    <line x1="12" y1="0" x2="12" y2="659" stroke="var(--folder-line)" stroke-width="1"/>
    <line x1="24" y1="0" x2="24" y2="659" stroke="var(--folder-line)" stroke-width="1"/>
    <line x1="31" y1="0" x2="31" y2="659" stroke="var(--folder-line)" stroke-width="1"/>
  </svg>
  <div class="folder__brand">STRUCTAVOLT</div>
  <div class="folder__circuit" role="img" aria-label="Light green circuit-line pattern"></div>
</section>

</body>
</html>
```